Friendly website/webshop needed for small family store

Hello .. I really need a website that is easy to use as I have no experience with this at all. ..
My shop is called quillmoss and I had a fantastic logo from craft forge - I asked for something mid century modern and I love it. I will attach . There might be some development around the logo now for various paraphernalia ( stickers , printed tissue paper carrier bags etc.. ) I would also like some sort of help with a slogan such as 'Live gently, gift kindly' as in,  live your best life etc..  but I'm not sure if this is a little trite .... ? but it would be nice to link the quillmoss with a little Motto.    If I need to pay extra for this - please could you let me know ... I'm happy to add on payment ..
As you can see the only LOGO colours really are grey black and orange .. so I would like some ideas to expand on the bird  to bring in some more colours.....  the tag line flower.children.home I would like to drop..
* the original brief included flowers on the tag line  because at the time we were also a florist . we now just sell dried flowers
My shop is in the beautiful town of Malvern, we have lots of tourist that come to walk the hills and enjoy nature - it's a family and dog friendly sort of town and we are a dog and family friendly sort of shop :-) It's a relaxed space that focuses on beautiful handmade items such as baskets & wooden utensils  from Africa, textiles from India and ceramics from France, Portugal and Italy.  We have a lovely section for children that sells beautiful soft toys from Charmel Duvo and the wonderful mice family and bunnies from Tornby.
We stock OBRETI homeware which is lovely and earthy and natural.
We would like to communicate the value of buying thoughtfully  and conscientiously, of building a beautiful home whilst investing in & supporting makers world wide. We don't sell anything that can't be repurposed, recycled etc..
Thank you

```html
<!DOCTYPE html>
<html lang="en">
<head>
<meta charset="utf-8">
<title>quillmoss – Live gently, gift kindly</title>
<link href="https://fonts.googleapis.com/css2?family=Bowlby+One&family=Jost:wght@400;500;600&display=swap" rel="stylesheet">
<style>
:root{
  --salmon:#d4897a;
  --blue:#6aa8be;
  --ink:#1d1d1d;
  --text:#3a3a3a;
  --sand:#e8e4e0;
  --white:#ffffff;
  --card-shadow:0 4px 14px rgba(0,0,0,.08);
}
*{box-sizing:border-box;margin:0;padding:0}
html,body{width:1200px;height:4570px;overflow:hidden}
body{font-family:'Jost',sans-serif;color:var(--text);background:var(--white);position:relative}
.abs{position:absolute}
.display{font-family:'Bowlby One',sans-serif;color:var(--ink);text-transform:uppercase;letter-spacing:1px;line-height:1.18}
.btn{position:absolute;background:var(--salmon);color:#fff;font-weight:600;font-size:16px;letter-spacing:1px;border-radius:28px;display:flex;align-items:center;justify-content:center;text-transform:uppercase}
.rule{position:absolute;height:2px;width:60px;background:var(--salmon)}
.para{position:absolute;font-size:14.5px;line-height:22.5px;color:var(--text)}

/* header */
.brand-name{font-weight:600;font-size:30px;color:var(--ink);letter-spacing:.5px}
.brand-dot{width:22px;height:22px;border-radius:50%;background:var(--salmon)}
.brand-tag{font-size:10px;font-weight:600;color:var(--blue);letter-spacing:.6px}
.contact-icon{width:40px;height:40px;border-radius:50%;background:var(--salmon);display:flex;align-items:center;justify-content:center}
.contact-label{font-size:13px;font-weight:600;color:var(--salmon);letter-spacing:1px}
.contact-value{font-size:22px;font-weight:500;color:var(--blue)}
.nav a{position:absolute;top:122px;font-size:14.5px;color:var(--ink);text-decoration:none;font-weight:500}
.nav a.active{color:var(--salmon)}
.nav a.active::after{content:"";position:absolute;left:0;right:0;bottom:-9px;height:2px;background:var(--salmon)}

/* hero */
.hero{left:0;top:175px;width:1200px;height:578px;background:linear-gradient(135deg,#8a6a4a 0%,#c9a57a 40%,#7fa39a 70%,#b98a72 100%)}
.hero-title{position:absolute;top:180px;width:100%;text-align:center;font-size:50px;color:#fff;text-shadow:0 2px 6px rgba(0,0,0,.35)}
.dots{position:absolute;top:512px;left:550px;display:flex;gap:16px}
.dots span{width:12px;height:12px;border-radius:50%;background:rgba(255,255,255,.6)}
.dots span.on{background:#fff}

/* categories */
.cat{position:absolute;width:457px;height:333px;border-radius:12px;overflow:hidden}
.cat-pill{position:absolute;left:30px;bottom:66px;border:1.5px solid #fff;border-radius:14px;color:#fff;font-size:13px;padding:3px 11px;text-transform:uppercase}
.cat-title{position:absolute;left:30px;bottom:24px;font-size:19px;color:#fff}
.cat-badge{left:560px;top:1110px;width:80px;height:80px;border-radius:50%;background:#fff;box-shadow:0 2px 8px rgba(0,0,0,.15)}

/* products */
.prod{position:absolute;width:222px;height:270px;background:#fff;border-radius:8px;box-shadow:var(--card-shadow);text-align:center}
.prod-img{position:absolute;left:56px;top:26px;width:110px;height:110px;border-radius:14px}
.prod-name{position:absolute;top:172px;width:100%;font-size:14.5px;font-weight:500;color:var(--ink);text-transform:uppercase}
.prod-desc{position:absolute;top:205px;width:100%;font-size:14px;line-height:22px;color:var(--text)}

/* footer */
.foot-head{position:absolute;font-size:14px;font-weight:600;color:var(--ink);text-transform:uppercase;letter-spacing:.5px}
.foot-line{position:absolute;height:2px;background:var(--ink)}
.foot-item{position:absolute;font-size:12.5px;line-height:17px;color:var(--text)}
.foot-icon{position:absolute;width:22px;height:22px;border-radius:50%;background:var(--salmon)}
</style>
</head>
<body>

<header>
  <div class="abs" style="left:134px;top:58px;display:flex;align-items:center;gap:8px">
    <span class="brand-dot"></span><span class="brand-name">quillmoss</span>
  </div>
  <div class="abs brand-tag" style="left:134px;top:136px">LIVE GENTLY, GIFT KINDLY</div>

  <div class="abs contact-icon" style="left:500px;top:44px">
    <svg width="20" height="16" viewBox="0 0 20 16"><rect x="1" y="1" width="18" height="14" rx="2" fill="none" stroke="#fff" stroke-width="1.6"/><path d="M1 2l9 7 9-7" fill="none" stroke="#fff" stroke-width="1.6"/></svg>
  </div>
  <div class="abs contact-label" style="left:558px;top:40px">EMAIL US</div>
  <div class="abs contact-value" style="left:558px;top:60px">info@quillmoss-uk.com</div>

  <div class="abs contact-icon" style="left:850px;top:44px">
    <svg width="20" height="20" viewBox="0 0 24 24"><path d="M6 3l3 5-2 2a11 11 0 0 0 7 7l2-2 5 3-2 4C11 22 2 13 2 5z" fill="none" stroke="#fff" stroke-width="1.6"/></svg>
  </div>
  <div class="abs contact-label" style="left:908px;top:40px">CALL US</div>
  <div class="abs contact-value" style="left:908px;top:60px">01632 960 418</div>

  <nav class="nav">
    <a class="active" href="#" style="left:357px">HOME</a>
    <a href="#" style="left:442px">BASKETS &amp; WOODEN UTENSILS</a>
    <a href="#" style="left:698px">TEXTILES</a>
    <a href="#" style="left:797px">CERAMICS</a>
    <a href="#" style="left:910px">TOYS</a>
    <a href="#" style="left:978px">CONTACT US</a>
  </nav>
</header>

<section class="abs hero" role="img" aria-label="Shop interior with woven baskets, ceramic birds and mugs on wooden shelves">
  <h1 class="display hero-title">Discover the perfect gift</h1>
  <div class="btn" style="left:513px;top:272px;width:174px;height:52px">Read more</div>
  <div class="dots"><span></span><span class="on"></span><span></span><span></span></div>
</section>

<section>
  <div class="cat" style="left:134px;top:805px;background:linear-gradient(160deg,#c8a66a,#7d6a52)" role="img" aria-label="Wooden vases and utensils">
    <span class="cat-pill">Africa</span><span class="display cat-title">Baskets &amp; wooden utensils</span>
  </div>
  <div class="cat" style="left:609px;top:805px;background:linear-gradient(160deg,#5a5d7a,#8d6b6f,#3d4a5a)" role="img" aria-label="Fan of colourful fabric swatches">
    <span class="cat-pill">India</span><span class="display cat-title">Textiles</span>
  </div>
  <div class="cat" style="left:134px;top:1166px;background:linear-gradient(160deg,#2d3a55,#9a948a,#5a4a3a)" role="img" aria-label="Glazed ceramic vases">
    <span class="cat-pill">France, Portugal and Italy</span><span class="display cat-title">Ceramics</span>
  </div>
  <div class="cat" style="left:609px;top:1166px;background:linear-gradient(160deg,#7a4a6a,#c88a6a,#3a2a3a)" role="img" aria-label="Shelf of soft plush toys">
    <span class="cat-pill">Charmel Duvo</span><span class="display cat-title">Soft toys</span>
  </div>
  <div class="abs cat-badge"></div>
</section>

<section class="abs" style="left:0;top:1572px;width:1200px;height:489px;background:var(--sand)">
  <div class="abs" style="left:133px;top:0;width:458px;height:489px;background:linear-gradient(180deg,#8a5a4a 0%,#d9d6d0 25%,#e8e6e2 60%,#6a6258 100%)" role="img" aria-label="Shop front with large windows and baskets outside"></div>
  <h2 class="display abs" style="left:650px;top:40px;font-size:42px">Welcome to<br><span style="color:var(--blue)">quillmoss</span></h2>
  <div class="rule" style="left:650px;top:175px"></div>
  <p class="para" style="left:650px;top:210px;width:420px">Lorem ipsum dolor sit amet, consectetur adipiscing elit, sed do eiusmod tempor incididunt ut labore et dolore magna aliqua. Ut enim ad minim veniam, quis nostrud exercitation ullamco laboris nisi ut aliquip ex ea commodo consequat. Duis aute irure dolor in reprehenderit in voluptate velit esse cillum dolore eu fugiat nulla pariatur. Excepteur sint occaecat cupidatat non proident, sunt in culpa qui officia deserunt mollit anim id est labo</p>
  <div class="btn" style="left:652px;top:396px;width:152px;height:44px;font-size:15px">Read more</div>
</section>

<section>
  <h2 class="display abs" style="left:0;top:2130px;width:1200px;text-align:center;font-size:42px">Our products</h2>
  <div class="rule" style="left:570px;top:2228px"></div>

  <div class="prod" style="left:133px;top:2290px"><div class="prod-img" style="background:#efe3dc" role="img" aria-label="Thin cord bracelet"></div><div class="prod-name">Luna style bracket</div><div class="prod-desc">Handmade Luna<br>Style Bracket</div></div>
  <div class="prod" style="left:371px;top:2290px"><div class="prod-img" style="background:#d9d8d2" role="img" aria-label="Bracelet on a gift card"></div><div class="prod-name">Juno bracelet</div><div class="prod-desc">A lovely Bracelet<br>Juno style</div></div>
  <div class="prod" style="left:609px;top:2290px"><div class="prod-img" style="background:linear-gradient(180deg,#e07aa0,#8cc060)" role="img" aria-label="Bouquet in a green box"></div><div class="prod-name">Through the rainbow</div><div class="prod-desc">A lovely Bracelet<br>Juno style</div></div>
  <div class="prod" style="left:847px;top:2290px"><div class="prod-img" style="background:linear-gradient(180deg,#f0b8c8,#7aa870)" role="img" aria-label="Flower arrangement in a pot"></div><div class="prod-name">Pot of happiness</div><div class="prod-desc">A lovely Bracelet<br>Juno style</div></div>

  <div class="prod" style="left:133px;top:2582px"><div class="prod-img" style="background:linear-gradient(135deg,#e8c040,#d05040,#4a80c0)" role="img" aria-label="Pile of colourful toys"></div><div class="prod-name">Toys</div><div class="prod-desc">Handmade Luna<br>Style Bracket</div></div>
  <div class="prod" style="left:371px;top:2582px"><div class="prod-img" style="background:linear-gradient(180deg,#9ac0b0,#d08040)" role="img" aria-label="Painted ceramic bowl"></div><div class="prod-name">Ceramics</div><div class="prod-desc">A lovely Bracelet<br>Juno style</div></div>
  <div class="prod" style="left:609px;top:2582px"><div class="prod-img" style="background:linear-gradient(180deg,#a8c0d8,#c89868)" role="img" aria-label="Folded clothes in a basket"></div><div class="prod-name">Clothings</div><div class="prod-desc">A lovely Bracelet<br>Juno style</div></div>
  <div class="prod" style="left:847px;top:2582px"><div class="prod-img" style="background:#d8b890" role="img" aria-label="Woven basket held by hand"></div><div class="prod-name">Baskets</div><div class="prod-desc">A lovely Bracelet<br>Juno style</div></div>

  <div class="btn" style="left:495px;top:2905px;width:211px;height:44px;font-size:15px">View all products</div>
</section>

<section class="abs" style="left:0;top:3026px;width:1200px;height:528px;background:var(--sand)">
  <h2 class="display abs" style="left:134px;top:50px;font-size:42px">Handmade<br>with love</h2>
  <div class="rule" style="left:134px;top:186px"></div>
  <p class="para" style="left:134px;top:220px;width:420px">Lorem ipsum dolor sit amet, consectetur adipiscing elit, sed do eiusmod tempor incididunt ut labore et dolore magna aliqua. Ut enim ad minim veniam, quis nostrud exercitation ullamco laboris nisi ut aliquip ex ea commodo consequat. Duis aute irure dolor in reprehenderit in voluptate velit esse cillum dolore eu fugiat nulla pariatur. Excepteur sint occaecat cupidatat non proident, sunt in culpa qui officia deserunt mollit anim id est labo</p>
  <div class="btn" style="left:135px;top:410px;width:152px;height:44px;font-size:15px">Read more</div>
  <div class="abs" style="left:582px;top:0;width:485px;height:528px;background:linear-gradient(160deg,#6a7a4a,#c89a6a 50%,#8a6a4a)" role="img" aria-label="Corner of the shop with plants, baskets and rattan chair"></div>
</section>

<section class="abs" style="left:0;top:3554px;width:1200px;height:628px;background:var(--white)">
  <div class="abs" style="left:134px;top:0;width:453px;height:628px;background:linear-gradient(160deg,#8a9a8a,#c8b49a 50%,#6a5a48)" role="img" aria-label="Display of small toy tins, candles and treats"></div>
  <h2 class="display abs" style="left:663px;top:130px;font-size:42px">Small<br>family store</h2>
  <div class="rule" style="left:663px;top:250px"></div>
  <p class="para" style="left:663px;top:285px;width:420px">Lorem ipsum dolor sit amet, consectetur adipiscing elit, sed do eiusmod tempor incididunt ut labore et dolore magna aliqua. Ut enim ad minim veniam, quis nostrud exercitation ullamco laboris nisi ut aliquip ex ea commodo consequat. Duis aute irure dolor in reprehenderit in voluptate velit esse cillum dolore eu fugiat nulla pariatur. Excepteur sint occaecat cupidatat non proident, sunt in culpa qui officia deserunt mollit anim id est labo</p>
  <div class="btn" style="left:665px;top:480px;width:152px;height:44px;font-size:15px">Read more</div>
</section>

<footer class="abs" style="left:0;top:4182px;width:1200px;height:388px;background:var(--sand)">
  <div class="abs" style="left:136px;top:150px;display:flex;align-items:center;gap:10px">
    <span class="brand-dot" style="width:30px;height:30px"></span><span class="brand-name" style="font-size:38px">quillmoss</span>
  </div>
  <div class="abs" style="left:136px;top:208px;font-size:14px;font-weight:600;color:var(--salmon);letter-spacing:.8px">MAKERS HOMES GIFTS</div>

  <div class="foot-head" style="left:442px;top:60px">Contact us</div>
  <div class="foot-line" style="left:442px;top:84px;width:192px"></div>
  <span class="foot-icon" style="left:444px;top:112px"></span>
  <div class="foot-item" style="left:475px;top:110px">Hollin Row 14,<br>4410 Ashford Vale</div>
  <span class="foot-icon" style="left:444px;top:162px"></span>
  <div class="foot-item" style="left:475px;top:160px">Call Us<br>01632 960 418</div>
  <span class="foot-icon" style="left:444px;top:212px"></span>
  <div class="foot-item" style="left:475px;top:210px">E mail Us<br>info@quillmoss-uk.com</div>

  <div class="foot-head" style="left:720px;top:60px">Menu</div>
  <div class="foot-line" style="left:720px;top:84px;width:106px"></div>
  <div class="foot-item" style="left:720px;top:104px;line-height:24px">Home<br>Baskets &amp; wooden utensils<br>Textiles<br>Ceramics<br>Toys<br>Contact Us</div>

  <div class="foot-head" style="left:964px;top:60px">Follow us</div>
  <div class="foot-line" style="left:964px;top:84px;width:106px"></div>
  <span class="foot-icon" style="left:964px;top:118px"></span>
  <div class="foot-item" style="left:998px;top:114px">Like us on<br>FACEPAGE</div>
  <span class="foot-icon" style="left:964px;top:168px"></span>
  <div class="foot-item" style="left:998px;top:164px">Follow us on<br>LINKWORK</div>
  <span class="foot-icon" style="left:964px;top:218px"></span>
  <div class="foot-item" style="left:998px;top:214px">Follow us on<br>SNAPGRAM</div>

  <div class="abs" style="left:134px;top:302px;width:934px;height:1px;background:#9a9690"></div>
  <div class="abs" style="left:0;top:340px;width:1200px;text-align:center;font-size:12px;color:var(--text)">Copyright © 2024 All Rights Reserved</div>
</footer>

</body>
</html>
```